Refresh of far from plain IT company website

Our web site is starting to show it's age. You can see the existing site here: www.plumbwick.net. As a growing company we want to come across as a dynamic collection of IT experts.

We want to update the design so are open to any colour palette and look, but want to retain our current table logo. We use the logo on our business cards but with a white background - see the attached file, so you don't need to keep the brown or the green.

The design should consider the range of browsers that will be looking at the site - so please show how it will look on a wide screen laptop and a 768x1024 tablet.

We want to add some pages about our team and their skills, probably with photos of each person on the team.

This is an uncoded project - the PSD files of the design is required, not coding.
Updates

Thanks everyone for the submissions so far.  It's a holiday day in the UK today but we will get some feedback on the designs so far out to you.

Target Market(s)

Architects and other creative types looking for IT support

Industry/Entity Type

Business

Font styles to use
Serif
Sans Serif

Requirements
Must have
• Must look good on a laptop and an iPad.

```html
<!DOCTYPE html>
<html lang="en">
<head>
<meta charset="utf-8">
<title>plumbwick — IT support for business</title>
<link href="https://fonts.googleapis.com/css2?family=Open+Sans:ital,wght@0,400;0,600;0,700;1,400&display=swap" rel="stylesheet">
<style>
:root{
  --plum:#8a1650;
  --gold:#d9ad08;
  --ink:#333;
  --muted:#777;
  --rule:#e6e6e6;
  --soft:#f7f7f7;
  --footer:#2a2e35;
  --hero-a:#3a4756;
  --hero-b:#252d36;
}
*{box-sizing:border-box;margin:0;padding:0}
html,body{width:1200px;height:2429px;overflow:hidden}
body{font-family:"Open Sans",Arial,sans-serif;color:var(--ink);background:#fff;position:relative}
.abs{position:absolute}
.center{text-align:center}

/* header */
.site-header{left:0;top:0;width:1200px;height:66px;border-top:4px solid var(--plum);background:#fff;box-shadow:0 1px 3px rgba(0,0,0,.15);z-index:2}
.brand{display:flex;align-items:center;gap:10px;font-weight:700;font-size:31px;color:var(--plum);letter-spacing:-.5px}
.brand-mark{width:24px;height:24px;background:var(--gold)}
.site-header .brand{position:absolute;left:131px;top:12px}
.main-nav{position:absolute;right:130px;top:0;display:flex;gap:32px;height:62px;align-items:center}
.main-nav a{font-size:15px;color:#333;text-decoration:none;text-transform:uppercase;position:relative;height:62px;line-height:62px}
.main-nav a.active{color:var(--gold)}
.main-nav a.active::before{content:"";position:absolute;left:-6px;right:-6px;top:-4px;height:4px;background:var(--gold)}

/* hero */
.hero{left:0;top:66px;width:1200px;height:530px;background:linear-gradient(180deg,var(--hero-a),var(--hero-b))}
.hero-title{position:absolute;left:0;width:1200px;top:118px;color:#fff;font-size:64px;line-height:72px;font-weight:400;text-transform:uppercase}
.hero-title strong{display:block;font-weight:700}
.hero-sub{position:absolute;left:0;width:1200px;top:288px;color:#fff;font-size:17px;text-transform:uppercase}
.hero-cta{position:absolute;left:499px;top:342px;width:202px;height:47px;background:var(--gold);color:#fff;font-weight:700;font-size:17px;line-height:47px;border-radius:2px}
.hero-arrow{position:absolute;top:242px;width:52px;height:48px;background:rgba(0,0,0,.55);display:flex;align-items:center;justify-content:center}
.hero-arrow.prev{left:0}.hero-arrow.next{right:0}

/* section heads */
.section-title{font-size:28px;font-weight:700;color:var(--plum);text-transform:uppercase}
.section-title span{color:var(--gold)}
.section-lede{font-size:15px;line-height:24px;text-transform:uppercase;color:#333;width:760px;margin:14px auto 0}
.divider{width:176px;height:4px;margin:18px auto 0;background:linear-gradient(90deg,var(--plum) 50%,var(--gold) 50%)}

.welcome{left:0;top:596px;width:1200px;height:442px;padding-top:40px}
.services{position:absolute;top:190px;left:0;width:1200px}
.service{position:absolute;width:176px;margin-left:-88px;text-align:center}
.service .badge{width:100px;height:100px;border-radius:50%;background:var(--gold);margin:0 auto;display:flex;align-items:center;justify-content:center}
.service h3{font-size:12.5px;font-weight:600;color:var(--plum);margin-top:16px;text-transform:uppercase;white-space:nowrap;letter-spacing:-.1px}
.service p{font-size:13px;line-height:19px;color:var(--muted);margin-top:5px;padding:0 6px}

.articles{left:0;top:1038px;width:1200px;height:503px;background:var(--soft);border-top:1px solid var(--rule);padding-top:37px}
.article{position:absolute;top:192px;width:292px}
.article .photo{width:290px;height:156px;border:1px solid #ccc}
.article h3{font-size:13px;font-weight:600;color:var(--plum);margin-top:15px;text-transform:uppercase}
.article p{font-size:12.5px;line-height:19px;color:#555;margin-top:8px}

.cta-band{left:0;top:1541px;width:1200px;height:156px;background:var(--gold)}
.cta-band h2{position:absolute;left:0;width:1200px;top:28px;color:#fff;font-size:45px;font-weight:700;text-transform:uppercase}
.remote{position:absolute;left:397px;top:1643px;display:flex;align-items:center}
.remote label{color:#fff;font-weight:700;font-size:23px;margin-right:16px}
.remote .field{width:116px;height:34px;background:#fff;border:1px solid #ddd;font-size:16px;color:#666;line-height:32px;padding-left:10px}
.remote .go{width:44px;height:34px;background:var(--plum);color:#fff;font-weight:700;font-size:17px;line-height:34px;text-align:center}

.news{left:0;top:1697px;width:1200px;height:492px;padding-top:36px}
.news-card{position:absolute;top:186px;width:290px;height:275px;background:#fff;box-shadow:0 1px 5px rgba(0,0,0,.18);padding:24px 10px 0 14px}
.news-card .date{font-size:12.5px;color:var(--gold);line-height:17px}
.news-card h3{margin-top:8px;font-size:13.5px;line-height:23px;font-weight:600;color:var(--plum);text-transform:uppercase;letter-spacing:-.2px}
.news-card p{margin-top:12px;padding-right:4px;font-size:12.5px;line-height:21px;color:#888}
.news-card .foot{position:absolute;left:0;right:0;top:236px;border-top:1px solid var(--rule);padding:8px 14px;font-size:13px;font-style:italic;color:var(--gold)}

/* footer */
.site-footer{left:0;top:2189px;width:1200px;height:240px;background:var(--footer);color:#ddd}
.footer-col{position:absolute;top:34px}
.footer-col h4{font-size:17px;font-weight:400;color:#fff;text-transform:uppercase}
.footer-col p{font-size:12.5px;line-height:21px;margin-top:10px}
.footer-col .mail{color:var(--gold)}
.footer-sep{position:absolute;left:544px;top:36px;width:1px;height:78px;background:#555}
.join{position:absolute;left:593px;top:32px;font-size:17px;color:#fff}
.subscribe{position:absolute;left:594px;top:71px;width:293px;height:39px;background:#fff;font-size:12.5px;color:#444;line-height:39px;padding-left:14px}
.subscribe .go{position:absolute;right:2px;top:2px;width:40px;height:35px;background:var(--plum);color:#fff;font-weight:700;font-size:19px;line-height:35px;text-align:center;padding:0}
.socials{position:absolute;left:903px;top:72px;display:flex;gap:3px}
.socials span{width:38px;height:38px;border:1px solid #ccc;display:block}
.footer-rule{position:absolute;left:130px;width:940px;top:154px;height:1px;background:#444}
.site-footer .brand{position:absolute;left:131px;top:180px;font-size:31px}
.legal{position:absolute;right:130px;top:187px;font-size:12.5px;color:#ddd;word-spacing:2px}
</style>
</head>
<body>

<header class="site-header abs">
  <div class="brand"><span class="brand-mark"></span>plumbwick</div>
  <nav class="main-nav">
    <a class="active">Home</a><a>About us</a><a>What we do</a><a>News blog</a><a>Articles</a><a>Clients</a><a>Partners</a>
  </nav>
</header>

<section class="hero abs" role="img" aria-label="Dusky city skyline photograph behind the headline">
  <h1 class="hero-title center">Serious IT<strong>SUPPORT FOR BUSINESS</strong></h1>
  <p class="hero-sub center">IT service for ambitious growing companies across all industry sectors</p>
  <div class="hero-cta center">GET STARTED NOW!!</div>
  <div class="hero-arrow prev"><svg width="16" height="24" viewBox="0 0 16 24"><path d="M12 3 4 12l8 9" fill="none" stroke="#fff" stroke-width="3.5"/></svg></div>
  <div class="hero-arrow next"><svg width="16" height="24" viewBox="0 0 16 24"><path d="M4 3l8 9-8 9" fill="none" stroke="#fff" stroke-width="3.5"/></svg></div>
</section>

<section class="welcome abs center">
  <h2 class="section-title">Welcome to plumb<span>wick</span></h2>
  <p class="section-lede">plumbwick was established with a specific aim: to consistently deliver an advanced and comprehensive IT service for ambitious growing companies across all industry sectors.</p>
  <div class="divider"></div>
  <div class="services">
    <div class="service" style="left:214px">
      <div class="badge"><svg width="56" height="56" viewBox="0 0 56 56" fill="none" stroke="#fff" stroke-width="5"><circle cx="28" cy="28" r="21"/><circle cx="28" cy="28" r="9"/><path d="M13 13l9 9M43 13l-9 9M13 43l9-9M43 43l-9-9"/></svg></div>
      <h3>IT Support &amp; Management</h3>
      <p>We metus volutpum ligula by oncus condimentum, and maec enas with etiam non lectus sa laoreet them.</p>
    </div>
    <div class="service" style="left:405px">
      <div class="badge"><svg width="62" height="50" viewBox="0 0 62 50" fill="none" stroke="#fff" stroke-width="4"><path d="M17 40H12a10 10 0 0 1 0-20 16 16 0 0 1 31-4 12 12 0 0 1 7 24h-5"/><path d="M31 44V22M22 30l9-9 9 9"/></svg></div>
      <h3>Cloud Computing</h3>
      <p>We metus volutpum ligula by oncus condimentum, and maec enas with etiam non lectus sa laoreet them.</p>
    </div>
    <div class="service" style="left:594px">
      <div class="badge"><svg width="54" height="54" viewBox="0 0 54 54"><circle cx="36" cy="18" r="13" fill="#fff"/><circle cx="40" cy="14" r="4" fill="var(--gold)"/><path d="M28 26 8 46l4 4 4-4 4 4 4-4-4-4 12-12" fill="#fff"/></svg></div>
      <h3>Disaster Recovery</h3>
      <p>We metus volutpum ligula by oncus condimentum, and maec enas with etiam non lectus sa laoreet them.</p>
    </div>
    <div class="service" style="left:790px">
      <div class="badge"><svg width="50" height="46" viewBox="0 0 50 46"><rect x="2" y="2" width="46" height="32" rx="2" fill="#fff"/><rect x="8" y="8" width="34" height="20" fill="var(--gold)"/><rect x="20" y="34" width="10" height="6" fill="#fff"/><rect x="13" y="40" width="24" height="4" fill="#fff"/></svg></div>
      <h3>Virtualisation</h3>
      <p>We metus volutpum ligula by oncus condimentum, and maec enas with etiam non lectus sa laoreet them.</p>
    </div>
    <div class="service" style="left:983px">
      <div class="badge"><svg width="54" height="54" viewBox="0 0 54 54" stroke="#fff" stroke-linecap="round"><path d="M10 44 36 18" stroke-width="6"/><circle cx="40" cy="14" r="8" fill="none" stroke-width="5"/><path d="M44 44 20 20" stroke-width="6"/><path d="M8 8l10 4 2 8-8-2z" fill="#fff" stroke-width="2"/></svg></div>
      <h3>CAD Services</h3>
      <p>We metus volutpum ligula by oncus condimentum, and maec enas with etiam non lectus sa laoreet them.</p>
    </div>
  </div>
</section>

<section class="articles abs center">
  <h2 class="section-title">Articles <span>latest</span></h2>
  <p class="section-lede">plumbwick was established with a specific aim: to consistently deliver an advanced and comprehensive IT service for ambitious growing companies across all industry sectors.</p>
  <div class="divider"></div>
  <article class="article" style="left:130px;text-align:left">
    <div class="photo" role="img" aria-label="Photo of colleagues reviewing documents at a desk" style="background:linear-gradient(135deg,#5c6f86,#b9a58e)"></div>
    <h3>Neque porro quisquam est qui do</h3>
    <p>Lorem ipsum dolor sit amet, consectetur adipisicing elit, sed do eiusmod tempor incididunt ut labore et dolore magna aliqua. Ut enim ad minim veniam, quis nostrud exercitation ullamco.</p>
  </article>
  <article class="article" style="left:453px;text-align:left">
    <div class="photo" role="img" aria-label="Photo of a business team standing in a row" style="background:linear-gradient(180deg,#2b2b2b,#6a6a6a)"></div>
    <h3>Neque porro quisquam est qui do</h3>
    <p>Lorem ipsum dolor sit amet, consectetur adipisicing elit, sed do eiusmod tempor incididunt ut labore et dolore magna aliqua. Ut enim ad minim veniam, quis nostrud exercitation ullamco.</p>
  </article>
  <article class="article" style="left:777px;text-align:left">
    <div class="photo" role="img" aria-label="Photo of business people in front of a world map" style="background:linear-gradient(135deg,#3f79b8,#a9cbe8)"></div>
    <h3>Neque porro quisquam est qui do</h3>
    <p>Lorem ipsum dolor sit amet, consectetur adipisicing elit, sed do eiusmod tempor incididunt ut labore et dolore magna aliqua. Ut enim ad minim veniam, quis nostrud exercitation ullamco.</p>
  </article>
</section>

<section class="cta-band abs">
  <h2 class="center">Need to grow your business</h2>
</section>
<div class="remote abs">
  <label>REMOTE</label>
  <div class="field">SESSION ID</div>
  <div class="go">GO</div>
</div>

<section class="news abs center">
  <h2 class="section-title">News <span>latest</span></h2>
  <p class="section-lede">plumbwick was established with a specific aim: to consistently deliver an advanced and comprehensive IT service for ambitious growing companies across all industry sectors.</p>
  <div class="divider"></div>
  <article class="news-card" style="left:132px;text-align:left">
    <div class="date">Dec 19, 2013</div>
    <h3>Neque porro quisquam est qui<br>dolorem ipsum quia dolor sit amet</h3>
    <p>Vivamus pellentesque quis massa vitae tristi que lorem tempor. Phasellus dapibus velit quam vel turpis dapibus, hendrerit velit vitae, tincidunt quam. Mauris a dui feugiat, ullamcorper erat vel, accumsan nisi...</p>
    <div class="foot">Read More</div>
  </article>
  <article class="news-card" style="left:453px;text-align:left">
    <div class="date">Dec 19, 2013</div>
    <h3>Neque porro quisquam est qui<br>dolorem ipsum quia dolor sit amet</h3>
    <p>Vivamus pellentesque quis massa vitae tristi que lorem tempor. Phasellus dapibus velit quam vel turpis dapibus, hendrerit velit vitae, tincidunt quam. Mauris a dui feugiat, ullamcorper erat vel, accumsan nisi...</p>
    <div class="foot">Read More</div>
  </article>
  <article class="news-card" style="left:777px;text-align:left">
    <div class="date">Dec 19, 2013</div>
    <h3>Neque porro quisquam est qui<br>dolorem ipsum quia dolor sit amet</h3>
    <p>Vivamus pellentesque quis massa vitae tristi que lorem tempor. Phasellus dapibus velit quam vel turpis dapibus, hendrerit velit vitae, tincidunt quam. Mauris a dui feugiat, ullamcorper erat vel, accumsan nisi...</p>
    <div class="foot">Read More</div>
  </article>
</section>

<footer class="site-footer abs">
  <div class="footer-col" style="left:130px">
    <h4>Contact us</h4>
    <p>T: 020 7946 0312<br>F: 020 7946 0318<br><span class="mail">Email: website@plumbwick.com</span></p>
  </div>
  <div class="footer-col" style="left:342px">
    <h4>Office address</h4>
    <p>Plumbwick.net Ltd, Harrow Court<br>48-52 Mill Lane London N1<br>4QT United Kingdom</p>
  </div>
  <div class="footer-sep"></div>
  <div class="join">Join us to start receiving the latest news, reviews and offers</div>
  <div class="subscribe">Enter youre email address:<div class="go">GO</div></div>
  <div class="socials"><span></span><span></span><span></span><span></span></div>
  <div class="footer-rule"></div>
  <div class="brand"><span class="brand-mark"></span>plumbwick</div>
  <div class="legal">© all Copyrights are reserved 2014 &nbsp;| &nbsp;Contact &nbsp;| &nbsp;Support &nbsp;| &nbsp;Terms</div>
</footer>

</body>
</html>
```